Brindovalle Business cards

Dear team, I need to get the design file to suit it to our team. The focus of the business card is the Automotive Market and the design must be in black colour and the logo must be in glossy black. On the front of the card I need to get the following info:

- Name and Surname
- Title
- eMail
- Phone Number
- Skype account
- domain address

```html
<!DOCTYPE html>
<html lang="en">
<head>
<meta charset="UTF-8">
<title>Brindovalle Business Cards</title>
<link href="https://fonts.googleapis.com/css2?family=Libre+Franklin:wght@400;600;800&display=swap" rel="stylesheet">
<style>
  :root {
    --bg: #141414;
    --card: #1c1c1c;
    --card-edge: #262626;
    --gloss: #0a0a0a;
    --white: #f4f4f4;
    --red: #e8262b;
    --muted: #dcdcdc;
  }
  * { margin: 0; padding: 0; box-sizing: border-box; }
  html, body { width: 1200px; height: 900px; overflow: hidden; }
  body {
    background: radial-gradient(ellipse at 50% 40%, #222 0%, var(--bg) 70%);
    font-family: "Libre Franklin", Arial, sans-serif;
    position: relative;
  }
  .card {
    position: absolute;
    left: 250px;
    width: 700px;
    height: 400px;
    background: var(--card);
    border: 1px solid var(--card-edge);
    box-shadow: 0 18px 40px rgba(0,0,0,.6);
    overflow: hidden;
  }
  .card--back { top: 40px; display: flex; align-items: center; justify-content: center; }
  .card--front { top: 470px; }

  .brand { display: flex; align-items: center; gap: 16px; }
  .brand__mark { width: 46px; height: 46px; background: var(--red); }
  .brand__name {
    font-weight: 800;
    font-size: 54px;
    color: var(--gloss);
    letter-spacing: .5px;
  }

  .wordmark {
    position: absolute; left: 48px; top: 40px;
    font-weight: 800; font-size: 36px; color: var(--white);
  }
  .contact { position: absolute; left: 48px; top: 118px; color: var(--muted); }
  .contact__name {
    font-weight: 800; font-size: 30px; color: var(--red);
    letter-spacing: 1px; text-transform: uppercase;
  }
  .contact__title { font-size: 17px; margin-top: 2px; }
  .contact__address { font-size: 18px; line-height: 1.35; margin-top: 18px; }
  .contact__list { list-style: none; margin-top: 16px; font-size: 19px; line-height: 1.4; }
  .contact__list li { display: flex; align-items: center; gap: 8px; }
  .contact__icon { width: 14px; height: 14px; flex: none; }

  .emblem {
    position: absolute; right: 40px; top: 80px;
    width: 290px; height: 290px; border-radius: 50%;
    background: radial-gradient(circle at 40% 35%, #3a3a3a 0%, #151515 65%, #0c0c0c 100%);
  }
  .red-band { position: absolute; left: 0; right: 0; bottom: 0; height: 8px; background: var(--red); }
</style>
</head>
<body>
  <section class="card card--back">
    <div class="brand">
      <span class="brand__mark"></span>
      <span class="brand__name">Brindovalle.com</span>
    </div>
  </section>

  <section class="card card--front">
    <div class="wordmark">Brindovalle.com</div>
    <div class="contact">
      <div class="contact__name">Marlo Vennick</div>
      <div class="contact__title">Director</div>
      <div class="contact__address">2847 N Calder Ave, Fenwick,<br>Oregon 97310</div>
      <ul class="contact__list">
        <li>
          <svg class="contact__icon" viewBox="0 0 14 14"><path d="M3 1 L5.5 1 L6.5 4 L5 5.2 Q6.5 8.5 8.8 9 L10 7.5 L13 8.5 L13 11 Q12 13 10 13 Q2 11 1 3 Q1 1 3 1Z" fill="var(--red)"/></svg>
          541-220-6073
        </li>
        <li>
          <svg class="contact__icon" viewBox="0 0 14 14"><rect x="1" y="3" width="12" height="8" fill="var(--red)"/><path d="M1 3 L7 8 L13 3" stroke="var(--card)" stroke-width="1.2" fill="none"/></svg>
          info@brindovalle.com
        </li>
        <li>
          <svg class="contact__icon" viewBox="0 0 14 14"><circle cx="7" cy="7" r="5.5" fill="none" stroke="var(--red)" stroke-width="1.6"/></svg>
          brindovalle
        </li>
      </ul>
    </div>
    <div class="emblem" role="img" aria-label="Large glossy black brand emblem"></div>
    <div class="red-band"></div>
  </section>
</body>
</html>
```